Business Card Design Project

use presentation folder design and my logo and make 4 over 4 business cards

Industry/Entity Type

Business

Requirements
Must have
• use the design from my presentation folder and put my logo on it

Name
Title
phone
fax
email

```html
<!DOCTYPE html>
<html lang="en">
<head>
<meta charset="utf-8">
<title>Harborline Counseling – Business Card</title>
<link rel="stylesheet" href="https://fonts.googleapis.com/css2?family=Tinos:wght@400;700&display=swap">
<style>
  :root {
    --page-bg: #efebe6;
    --front-top: #e9dcd2;
    --front-bottom: #dccabd;
    --panel-beige: #e6ded1;
    --tile-grey: #e9e8e7;
    --card-white: #f7f7f6;
    --accent-copper: #b5652a;
    --band-brown: #a86d2a;
    --ink: #2b2724;
    --brand-grey: #8e8b88;
  }
  * { box-sizing: border-box; margin: 0; padding: 0; }
  html, body { width: 1200px; height: 900px; overflow: hidden; }
  body {
    background: var(--page-bg);
    font-family: "Tinos", "Times New Roman", serif;
    position: relative;
  }
  .card {
    position: absolute;
    left: 280px;
    width: 640px;
    height: 366px;
    overflow: hidden;
    box-shadow: 0 6px 18px rgba(0,0,0,0.12);
  }
  .card--front {
    top: 50px;
    background: linear-gradient(160deg, var(--front-top), var(--front-bottom));
    display: flex;
    align-items: center;
    justify-content: center;
  }
  .brand {
    display: flex;
    align-items: center;
    gap: 16px;
  }
  .brand__dot {
    width: 34px;
    height: 34px;
    border-radius: 50%;
    background: var(--accent-copper);
  }
  .brand__name {
    font-size: 44px;
    font-weight: 400;
    color: var(--brand-grey);
    letter-spacing: 0.5px;
  }
  .card--back {
    top: 466px;
    background: var(--card-white);
  }
  .card__shapes { position: absolute; inset: 0; }
  .back-brand {
    position: absolute;
    left: 30px;
    top: 70px;
    width: 160px;
    display: flex;
    flex-direction: column;
    align-items: center;
    gap: 10px;
    text-align: center;
  }
  .back-brand__dot {
    width: 26px; height: 26px; border-radius: 50%;
    background: var(--accent-copper);
  }
  .back-brand__name {
    font-size: 22px;
    line-height: 1.15;
    color: var(--brand-grey);
  }
  .contact {
    position: absolute;
    left: 295px;
    top: 92px;
    color: var(--ink);
  }
  .contact__name {
    font-size: 29px;
    font-weight: 400;
    letter-spacing: 1px;
    text-transform: uppercase;
  }
  .contact__title {
    font-size: 17px;
    margin-top: 2px;
  }
  .contact__list {
    list-style: none;
    margin-top: 36px;
    font-size: 17px;
    line-height: 22px;
  }
  .contact__label {
    display: inline-block;
    width: 26px;
    font-weight: 700;
    color: var(--accent-copper);
  }
</style>
</head>
<body>

  <section class="card card--front" aria-label="Card front">
    <div class="brand">
      <span class="brand__dot"></span>
      <span class="brand__name">Harborline Counseling</span>
    </div>
  </section>

  <section class="card card--back" aria-label="Card back">
    <svg class="card__shapes" width="640" height="366" viewBox="0 0 640 366" aria-hidden="true">
      <path d="M0 0 H205 V200 Q205 228 178 228 H0 Z" fill="var(--tile-grey)"/>
      <path d="M0 255 L300 366 H0 Z" fill="var(--band-brown)"/>
      <path d="M240 0 H640 V60 L555 30 Z" fill="var(--card-white)"/>
      <path d="M240 0 L555 30 L640 60 V366 H300 L265 352 Q225 338 232 300 Z" fill="var(--panel-beige)"/>
    </svg>

    <div class="back-brand">
      <span class="back-brand__dot"></span>
      <span class="back-brand__name">Harborline<br>Counseling</span>
    </div>

    <div class="contact">
      <h1 class="contact__name">Dalton Reyes</h1>
      <p class="contact__title">Operation Manager</p>
      <ul class="contact__list">
        <li><span class="contact__label">T</span>(221) 33 410 27 18</li>
        <li><span class="contact__label">F</span>(221) 77 582 64 31</li>
        <li><span class="contact__label">E</span>dalton@harborlinecounseling.com</li>
      </ul>
    </div>
  </section>

</body>
</html>
```